TV Antenna Installation business needs a unique flyer

We need a simple but effective flyer design for our TV Aerial installation company based in Newcastle, NSW, Australia called Bright Harbour TV & Aerial Svcs.
We are trying to target areas where there has been a new transmitter installed and most houses just require their aerial redirecting and tv's retuning.

Industry/Entity Type

Business

Requirements
Must have
• We would like the idea of a headline phrase such as " Poor TV reception……..now a thing from the past" or something similar & catchy.
Also "Did you know a new transmitter has been recently installed in your area, we can therefore now GUARANTEE 100% PERFECT PICTURE
Charges from only $95.
- Free 5 year warranty
- Free signal testing
- Free Onsite Quote
Phone 0463 527 209
Nice to have
• Other services include:

- New Installs
- Extra Points & repairs
- TV wall mounting/Home Cinema
- Pull down tall masts

Modern tv picture, see example uploaded

```html
<!DOCTYPE html>
<html lang="en">
<head>
<meta charset="utf-8">
<title>Bright Harbour TV &amp; Aerial Svcs – Flyer</title>
<link rel="stylesheet" href="https://fonts.googleapis.com/css2?family=Bree+Serif&family=Open+Sans:ital,wght@0,400;0,700;1,400&display=swap">
<style>
  :root {
    --green: #2db672;
    --white: #ffffff;
    --orange: #f39a1e;
    --screen-dark: #5e554d;
    --screen-light: #b9b3ab;
    --page: #f2f2f2;
  }
  * { margin: 0; padding: 0; box-sizing: border-box; }
  html, body { width: 897px; height: 1200px; overflow: hidden; background: var(--page); }
  .flyer { position: relative; width: 897px; height: 1200px; background: var(--white); }
  .panel {
    position: absolute; left: 17px; top: 16px; width: 867px; height: 1168px;
    background: var(--green);
  }
  .brand-tab { position: absolute; left: 332px; top: 16px; width: 552px; height: 128px; }
  .call {
    position: absolute; left: 62px; top: 46px;
    font-family: "Bree Serif", serif; color: var(--white); line-height: 1.15;
  }
  .call__label { font-size: 38px; }
  .call__phone { font-size: 37px; display: flex; align-items: center; gap: 6px; }
  .call__phone svg { width: 30px; height: 30px; }
  .brand {
    position: absolute; left: 420px; top: 52px; width: 450px;
    font-family: "Bree Serif", serif; font-size: 56px; color: var(--orange);
    display: flex; align-items: center; gap: 12px; white-space: nowrap;
  }
  .brand__dot { width: 18px; height: 18px; border-radius: 50%; background: var(--green); flex: none; }
  .tv-visual {
    position: absolute; left: 65px; top: 237px; width: 412px; height: 257px;
    border-radius: 14px;
    background: radial-gradient(ellipse at 40% 50%, var(--screen-light), var(--screen-dark));
  }
  .headline {
    position: absolute; left: 515px; top: 226px; width: 360px;
    font-family: "Bree Serif", serif; color: var(--white); white-space: nowrap;
  }
  .headline__main { font-size: 82px; line-height: 0.95; }
  .headline__sub { font-size: 72px; line-height: 1.05; }
  .headline__tag { font-size: 54px; line-height: 1.1; margin-top: 24px; }
  .intro {
    position: absolute; left: 62px; top: 535px; width: 778px;
    font-family: "Open Sans", sans-serif; font-size: 30px; line-height: 53px;
    color: var(--white); white-space: nowrap;
  }
  .intro__line { display: block; }
  .intro__line--justify { text-align: justify; text-align-last: justify; }
  .intro strong { font-weight: 700; }
  .offer {
    position: absolute; left: 94px; top: 720px; width: 708px; height: 260px;
    border: 4px dashed var(--white);
    text-align: center; color: var(--white);
  }
  .offer__price { font-family: "Bree Serif", serif; font-size: 60px; line-height: 1.2; margin-top: 10px; }
  .offer__list { list-style: none; font-family: "Open Sans", sans-serif; font-style: italic; font-size: 31px; line-height: 43px; margin-top: 12px; }
  .services {
    position: absolute; left: 62px; top: 1010px; color: var(--white);
    font-family: "Open Sans", sans-serif;
  }
  .services__title { font-size: 30px; font-weight: 700; margin-left: 6px; }
  .services__grid {
    list-style: none; display: grid; grid-template-columns: 338px 440px;
    font-size: 26px; line-height: 38px; margin-top: 10px;
  }
  .services__grid li { display: flex; align-items: center; gap: 6px; }
  .services__grid svg { width: 24px; height: 20px; flex: none; }
</style>
</head>
<body>
<div class="flyer">
  <div class="panel"></div>

  <svg class="brand-tab" viewBox="0 0 552 128" aria-hidden="true">
    <polygon points="0,0 552,0 552,128 65,128" fill="#ffffff"/>
  </svg>

  <div class="call">
    <div class="call__label">Call Us Today</div>
    <div class="call__phone">
      <svg viewBox="0 0 30 30" aria-hidden="true">
        <circle cx="15" cy="15" r="13" fill="none" stroke="#fff" stroke-width="2.5"/>
        <path d="M10 8c-2 3 1 10 6 13 2 1 3 1 4-1l-3-3-2 1c-2-1-3-3-4-5l1-2-2-3z" fill="#fff"/>
      </svg>
      <span>0463 527 209</span>
    </div>
  </div>

  <div class="brand"><span>Bright Harbour</span><span class="brand__dot"></span></div>

  <div class="tv-visual" role="img" aria-label="Retro television set showing a static-filled screen"></div>

  <div class="headline">
    <div class="headline__main">Poor TV</div>
    <div class="headline__sub">reception</div>
    <div class="headline__tag">NOW a thing<br>from the past</div>
  </div>

  <div class="intro">
    <span class="intro__line intro__line--justify">Did you know a new transmitter has been</span>
    <span class="intro__line">recently installed in your area, we can therefore</span>
    <span class="intro__line">now <strong>GUARANTEED 100% PERFECT PICTURE</strong></span>
  </div>

  <div class="offer">
    <div class="offer__price">Charges from only $95</div>
    <ul class="offer__list">
      <li>+ Free 5 years warranty</li>
      <li>+ Free signal testing</li>
      <li>+ Free Onsite Quote</li>
    </ul>
  </div>

  <div class="services">
    <div class="services__title">Other services include:</div>
    <ul class="services__grid">
      <li><svg viewBox="0 0 24 20" aria-hidden="true"><path d="M2 11l6 6L22 3" fill="none" stroke="#fff" stroke-width="3"/></svg>New Installs</li>
      <li><svg viewBox="0 0 24 20" aria-hidden="true"><path d="M2 11l6 6L22 3" fill="none" stroke="#fff" stroke-width="3"/></svg>TV wall mounting/Home Cinema</li>
      <li><svg viewBox="0 0 24 20" aria-hidden="true"><path d="M2 11l6 6L22 3" fill="none" stroke="#fff" stroke-width="3"/></svg>Extra Points &amp; repairs</li>
      <li><svg viewBox="0 0 24 20" aria-hidden="true"><path d="M2 11l6 6L22 3" fill="none" stroke="#fff" stroke-width="3"/></svg>Pull down tall masts</li>
    </ul>
  </div>
</div>
</body>
</html>
```